kolvarin.link kolvarin.space kolvarin.press website

The website is named KOLVARIN and it will have 3 domain names. kolvarin.link, press, space.
I'd like it to be viewed on Pads, pcs and phones.

page menu:

kolvarin.link(start page): presentation of company. (creative, design, app, new product innovation.)
Here we'll need sosial media icons: plimber, vendoloop, mirtavel, trelvanet. (light but some 'fruity' colors)

kolvarin.press: blog. It will be a 75% picture blog > rest will be text. I need to be able to resize pictures and shape columns to picture size. (light but some 'fruity' colors)

kolvarin.space : the fun part of this web design, however, on entering the page I'd like a non-disclosure agreement where viewer simply click "yes, I agree" after filling out contact info. (check attached document)
We will have space here for uploading PDF files viewers can download. There is also a blog space here to tell in brief about the PDF file. (maybe a space/sci-fi theme her e.g spacechimp, Laika the space dog?)

I will attach the logo here I want you to use > and develop for the .space .press webpage. The logo i uploaded is for the .link page.

Target Market(s)

venture capitalists

Number of Pages Required

3 page

Requirements
Must have
• a few 'fruity colors' but mostly white and grey

```html
<!DOCTYPE html>
<html lang="en">
<head>
<meta charset="utf-8">
<title>Kolvarin Link</title>
<link rel="stylesheet" href="https://fonts.googleapis.com/css2?family=Poppins:wght@500;600&family=Lato:wght@400;700;900&display=swap">
<style>
:root{
  --ink:#111111;
  --text:#333333;
  --muted:#666666;
  --orange:#e08a1e;
  --red:#e04a33;
  --green:#5a9a3e;
  --yellow:#f7ae1b;
  --grey-band:#f2f2f2;
  --line:#d6d6d6;
  --ornament:#e3a13a;
  --cream:#fbf7c4;
  --footer:#121212;
  --white:#ffffff;
}
*{box-sizing:border-box;margin:0;padding:0}
html,body{width:1200px;height:2261px;overflow:hidden}
body{position:relative;background:var(--white);font-family:"Lato",sans-serif;color:var(--text)}
.abs{position:absolute}

/* header */
.site-header{position:absolute;left:0;top:0;width:1200px;height:151px;background:var(--white)}
.brand{left:98px;top:18px;display:flex;align-items:center;gap:12px}
.brand-mark{width:22px;height:22px;background:var(--yellow)}
.brand-name{font-family:"Poppins",sans-serif;font-weight:600;font-size:34px;letter-spacing:1px;color:var(--ink);line-height:1}
.social-top{right:150px;top:22px;display:flex;gap:14px;font-size:13px;font-weight:700}
.social-top span{color:#2f4b8c}
.menu-btn{left:1062px;top:12px;width:38px;height:36px;border:2px solid var(--red);border-radius:3px;padding:7px 6px;display:flex;flex-direction:column;justify-content:space-between}
.menu-btn i{display:block;height:3px;background:var(--red)}
.contact{top:83px;display:flex;align-items:center;gap:9px}
.contact .ring{width:36px;height:36px;border:2px solid #9a9a9a;border-radius:50%;display:flex;align-items:center;justify-content:center}
.contact b{display:block;font-size:14px;color:var(--ink)}
.contact span{display:block;font-size:15px;color:#444;line-height:1.1}

/* hero */
.hero{position:absolute;left:0;top:151px;width:1200px;height:546px;background:linear-gradient(180deg,#d9dde0 0%,#e6e9eb 45%,#c9ced2 100%)}
.hero-bar{position:absolute;left:0;top:697px;width:1200px;height:6px;background:#c9ced6}
.hero-title{left:0;top:262px;width:1200px;text-align:center;font-family:"Poppins",sans-serif;font-weight:500;font-size:31px;color:#333;letter-spacing:.5px}
.btn-contact{left:523px;top:322px;width:154px;height:46px;background:var(--red);color:var(--white);border-radius:3px;font-weight:700;font-size:20px;display:flex;align-items:center;justify-content:center}
.hero-dots{left:567px;top:657px;display:flex;gap:8px}
.hero-dots i{width:11px;height:11px;border-radius:50%;background:#d7d7d7}
.hero-dots i:first-child{background:var(--yellow)}

/* about */
.about{position:absolute;left:0;top:703px;width:1200px;height:385px;background:var(--grey-band)}
.section-title{font-family:"Poppins",sans-serif;font-weight:600;font-size:37px;color:var(--ink);line-height:1}
.section-title em{font-style:normal;color:var(--orange)}
.about-title{left:99px;top:46px}
.about-rule{left:99px;top:108px;width:628px;height:1px;background:var(--line)}
.about-copy{left:99px;top:122px;width:640px;font-size:16.5px;line-height:30.5px;color:#333;white-space:nowrap}
.about-copy strong{display:block;color:var(--ink);font-weight:700}
.about-divider{left:772px;top:55px;width:1px;height:290px;background:linear-gradient(180deg,transparent,#d0d0d0,transparent)}
.inquiry-title{left:826px;top:46px}
.inquiry-form .field{position:absolute;left:826px;width:274px;height:32px;background:var(--white);border:1px solid #cfcfcf;border-radius:2px;font-size:12px;color:#555;padding:7px 8px}
.inquiry-form .field.area{height:65px}
.btn-submit{left:826px;top:311px;width:111px;height:34px;background:var(--red);color:var(--white);border-radius:2px;font-weight:900;font-size:16px;letter-spacing:1px;display:flex;align-items:center;justify-content:center;gap:8px}
.btn-submit .arrow{width:20px;height:20px;border-radius:50%;background:#3a3a3a;display:flex;align-items:center;justify-content:center}

/* offer */
.offer{position:absolute;left:0;top:1088px;width:1200px;height:600px;background:var(--white)}
.center-title{left:0;width:1200px;text-align:center}
.title-rule{left:380px;width:440px;height:1px;background:var(--line)}
.title-ornament{left:590px;width:20px;height:20px;border-radius:4px;background:var(--ornament)}
.services{left:99px;top:181px;width:1001px;height:353px;display:flex;border-radius:3px;overflow:hidden}
.service{flex:1;color:var(--white);text-align:center;padding-top:54px}
.service.design{background:var(--green)}
.service.apps{background:var(--red)}
.service.ideas{background:var(--yellow)}
.service svg{display:block;margin:0 auto;height:110px}
.service h3{margin-top:50px;font-family:"Lato",sans-serif;font-weight:900;font-size:19px;letter-spacing:.8px}
.service p{margin:20px auto 0;width:320px;font-size:14px;line-height:22px;white-space:nowrap}

/* testimonials */
.testimonials{position:absolute;left:0;top:1688px;width:1200px;height:520px;background:var(--cream)}
.quote-card{position:absolute;width:464px;height:142px;background:var(--white);border:1px solid #d8d8d8;border-radius:6px;padding:18px 18px 0 46px;font-size:12.3px;font-style:italic;line-height:20.5px;color:#333}
.quote-card .qmark{position:absolute;left:14px;top:14px}
.quote-tail{position:absolute}
.avatar{position:absolute;width:106px;height:106px;border-radius:50%;border:3px solid #e9753a;background:radial-gradient(circle at 50% 40%,#d9a98b,#8a5a40 75%)}
.quote-badge{position:absolute;width:44px;height:44px;border-radius:50%;background:var(--red);display:flex;align-items:center;justify-content:center}
.client{position:absolute;font-size:15px;color:#222;display:flex;gap:10px}
.client span{border-left:2px solid var(--orange);padding-left:10px}
.card-sep{left:600px;top:170px;width:1px;height:225px;background:linear-gradient(180deg,transparent,#ddd,transparent)}
.slider-dots{left:566px;top:457px;display:flex;gap:8px}
.slider-dots i{width:11px;height:11px;border-radius:50%;background:#cfcfcf}
.slider-dots i:first-child{background:var(--green)}

/* footer */
.site-footer{position:absolute;left:0;top:2208px;width:1200px;height:53px;background:var(--footer);color:#ddd}
.copyright{left:99px;top:18px;font-size:13px}
.social-foot{right:100px;top:17px;display:flex;gap:16px;font-size:13px;font-weight:700;color:var(--white)}
</style>
</head>
<body>

<header class="site-header">
  <div class="abs brand"><i class="brand-mark"></i><span class="brand-name">KOLVARIN</span></div>
  <nav class="abs social-top" aria-label="Social links">
    <span>mirtavel</span><span>plimber</span><span>trelvanet</span><span>vendoloop</span>
  </nav>
  <div class="abs menu-btn" aria-label="Menu"><i></i><i></i><i></i></div>
  <div class="abs contact" style="left:720px">
    <div class="ring"><svg width="18" height="18" viewBox="0 0 24 24"><path fill="#5a9a3e" d="M6.6 10.8a15 15 0 0 0 6.6 6.6l2.2-2.2c.3-.3.7-.4 1-.2 1.1.4 2.3.6 3.6.6.6 0 1 .4 1 1V20c0 .6-.4 1-1 1A17 17 0 0 1 3 4c0-.6.4-1 1-1h3.5c.6 0 1 .4 1 1 0 1.3.2 2.5.6 3.6.1.3 0 .7-.2 1z"/></svg></div>
    <div><b>Call Us</b><span>(555)-214-0386</span></div>
  </div>
  <div class="abs contact" style="left:907px">
    <div class="ring"><svg width="18" height="14" viewBox="0 0 20 14"><rect width="20" height="14" rx="1" fill="#5a9a3e"/><path d="M1 1l9 7 9-7" stroke="#fff" stroke-width="1.6" fill="none"/></svg></div>
    <div><b>Email Us</b><span>info@kolvarinlink.com</span></div>
  </div>
</header>

<section class="hero" role="img" aria-label="Illustrated workspace from above with a desktop monitor, a laptop, hands typing, coffee cups, notebooks and charts"></section>
<div class="hero-bar"></div>
<h1 class="abs hero-title">WE DESIGN &amp; DEVELOP YOUR DREAMS</h1>
<div class="abs btn-contact">CONTACT US</div>
<div class="abs hero-dots"><i></i><i></i><i></i><i></i></div>

<section class="about">
  <h2 class="abs section-title about-title">About <em>Kolvarin Link</em></h2>
  <div class="abs about-rule"></div>
  <div class="abs about-copy">
    <strong>Lorem ipsum dolor sit amet, consectetuer in the adipiscing elit...</strong>
    Lorem ipsum dolor sit amet, consectetuer adipiscing elit, sed diam nonummy nibh<br>
    euismod tincidunt ut laoreet dolore magna aliquam erat volutpat. Ut wisi enim ad<br>
    minim veniam, quis nostrud exercisei tation ullamcorper suscipit lobortis nisl ut<br>
    aliquip ex ea commodo consequat. Duis autem vel eumorl iriure dolor in hendrerit in<br>
    vulputate velit esse molestie consequat, vel illum dolore eu feugiat nullam facilisis at<br>
    vero eros et accumsan et iusto odio &nbsp;facilisi.....
  </div>
  <div class="abs about-divider"></div>
  <h2 class="abs section-title inquiry-title">Quick <em>Inquiry</em></h2>
  <form class="inquiry-form">
    <div class="field" style="top:106px">Name</div>
    <div class="field" style="top:147px">Email</div>
    <div class="field" style="top:189px">Phone</div>
    <div class="field area" style="top:231px">Messages</div>
  </form>
  <div class="abs btn-submit">SUBMIT <span class="arrow"><svg width="8" height="10" viewBox="0 0 8 10"><path d="M2 1l4 4-4 4" stroke="#fff" stroke-width="1.8" fill="none"/></svg></span></div>
</section>

<section class="offer">
  <h2 class="abs section-title center-title" style="top:52px">What We <em>Offer</em></h2>
  <div class="abs title-rule" style="top:121px"></div>
  <div class="abs title-ornament" style="top:111px" role="img" aria-label="Small fruit ornament"></div>
  <div class="abs services">
    <div class="service design">
      <svg viewBox="0 0 110 110" width="110"><rect x="4" y="4" width="102" height="102" rx="10" fill="#fff"/><rect x="16" y="30" width="78" height="64" fill="#5a9a3e"/><circle cx="18" cy="17" r="4" fill="#5a9a3e"/><circle cx="30" cy="17" r="4" fill="#5a9a3e"/><circle cx="42" cy="17" r="4" fill="#5a9a3e"/><path d="M40 48l28 28" stroke="#fff" stroke-width="7" stroke-linecap="round"/><circle cx="74" cy="81" r="6" fill="#fff"/></svg>
      <h3>CREATIVE DESIGN</h3>
      <p>Lorem ipsum dolor sit amet, sed diam<br>nonummy nibh euismod tincidunt ut laoreet<br>dolore. Lorem ipsum dolor sit amet</p>
    </div>
    <div class="service apps">
      <svg viewBox="0 0 110 110" width="110"><rect x="14" y="2" width="58" height="106" rx="9" fill="#fff"/><rect x="22" y="16" width="42" height="74" fill="#e04a33"/><rect x="28" y="26" width="10" height="6" fill="#fff"/><rect x="28" y="40" width="10" height="6" fill="#fff"/><rect x="28" y="54" width="10" height="6" fill="#fff"/><rect x="28" y="68" width="10" height="6" fill="#fff"/><circle cx="43" cy="99" r="4" fill="#e04a33"/><circle cx="76" cy="52" r="20" fill="#fff"/><circle cx="76" cy="52" r="27" fill="none" stroke="#fff" stroke-width="8" stroke-dasharray="8 6"/><circle cx="76" cy="52" r="8" fill="#e04a33"/></svg>
      <h3>APP DEVELOPMENT</h3>
      <p>Lorem ipsum dolor sit amet, sed diam<br>nonummy nibh euismod tincidunt ut laoreet<br>dolore. Lorem ipsum dolor sit amet</p>
    </div>
    <div class="service ideas">
      <svg viewBox="0 0 110 110" width="110"><path d="M30 108V84C14 74 10 58 14 42 20 18 40 8 60 10c24 2 38 20 38 42l10 18-10 4v14c0 6-4 10-10 10H82v10z" fill="#fff"/><circle cx="56" cy="46" r="16" fill="#f7ae1b"/><rect x="50" y="62" width="12" height="10" fill="#f7ae1b"/><path d="M56 20v-8M34 30l-6-6M78 30l6-6" stroke="#f7ae1b" stroke-width="3"/></svg>
      <h3>NEW PRODUCT INNOVATION</h3>
      <p>Lorem ipsum dolor sit amet, sed diam<br>nonummy nibh euismod tincidunt ut laoreet<br>dolore. Lorem ipsum dolor sit amet</p>
    </div>
  </div>
</section>

<section class="testimonials">
  <h2 class="abs section-title center-title" style="top:61px">Client <em>Testimonials</em></h2>
  <div class="abs title-rule" style="top:128px"></div>
  <div class="abs title-ornament" style="top:118px" role="img" aria-label="Small fruit ornament"></div>

  <div class="quote-card" style="left:112px;top:175px">
    <svg class="qmark" width="22" height="18" viewBox="0 0 22 18"><path d="M0 18V9L5 0h4L6 8h4v10zM12 18V9l5-9h4l-3 8h4v10z" fill="#c8c8c8"/></svg>
    Lorem ipsum dolor sit amet, sed diam nonummy nibh euismod tincidunt ut laoreet dolore. Lorem ipsum dolor sit amet, sed diam nonummy nibh euismod tincidunt ut laoreet dolore. Lorem ipsum dolor sit amet, sed diam nonummy nibh euismod tincidunt ut laoreet dolore.
  </div>
  <svg class="quote-tail" style="left:452px;top:316px" width="110" height="28" viewBox="0 0 110 28"><path d="M0 0L12 26 110 0" fill="#fff" stroke="#d8d8d8"/><rect x="1" y="-2" width="108" height="3" fill="#fff"/></svg>
  <div class="avatar" style="left:99px;top:275px" role="img" aria-label="Client portrait"></div>
  <div class="quote-badge" style="left:171px;top:341px"><svg width="18" height="14" viewBox="0 0 22 18"><path d="M0 18V9L5 0h4L6 8h4v10zM12 18V9l5-9h4l-3 8h4v10z" fill="#fff"/></svg></div>
  <div class="client" style="left:313px;top:351px">Odessa Grint<span>Customer</span></div>

  <div class="abs card-sep"></div>

  <div class="quote-card" style="left:637px;top:175px">
    <svg class="qmark" width="22" height="18" viewBox="0 0 22 18"><path d="M0 18V9L5 0h4L6 8h4v10zM12 18V9l5-9h4l-3 8h4v10z" fill="#c8c8c8"/></svg>
    Lorem ipsum dolor sit amet, sed diam nonummy nibh euismod tincidunt ut laoreet dolore. Lorem ipsum dolor sit amet, sed diam nonummy nibh euismod tincidunt ut laoreet dolore. Lorem ipsum dolor sit amet, sed diam nonummy nibh euismod tincidunt ut laoreet dolore.
  </div>
  <svg class="quote-tail" style="left:977px;top:316px" width="110" height="28" viewBox="0 0 110 28"><path d="M0 0L12 26 110 0" fill="#fff" stroke="#d8d8d8"/><rect x="1" y="-2" width="108" height="3" fill="#fff"/></svg>
  <div class="avatar" style="left:624px;top:275px" role="img" aria-label="Client portrait"></div>
  <div class="quote-badge" style="left:696px;top:341px"><svg width="18" height="14" viewBox="0 0 22 18"><path d="M0 18V9L5 0h4L6 8h4v10zM12 18V9l5-9h4l-3 8h4v10z" fill="#fff"/></svg></div>
  <div class="client" style="left:838px;top:351px">Odessa Grint<span>Customer</span></div>

  <div class="abs slider-dots"><i></i><i></i><i></i><i></i></div>
</section>

<footer class="site-footer">
  <p class="abs copyright">Copyright © 2016 &nbsp;Kolvarin Link. All Rights Reserved.</p>
  <nav class="abs social-foot" aria-label="Social links">
    <span>plimber</span><span>vendoloop</span><span>mirtavel</span><span>trelvanet</span>
  </nav>
</footer>

</body>
</html>
```